Real estate team needs a poster design to promote Free Listing competition

Need a poster design to promote a free listing competition we have about to get underway. It will run from Jan 1,2014 - June 30, 2014 (yes, I'm running late getting this piece organized :-) )! To win a free listing from us, videos need to be submitted that show why they should win the competition and get a free listing from us. It is voted on by the general public on our website. Website is currently being modified to incorporate this so it is not 'live' yet. Our team is TRHomesDirect.com.

I'd like to see designs with blue tones as a focus (our logo and branding is in blue), with some other complementary (and wow) colors incorporated. I'd like to have some depth to the poster, and like what I see with 3D text. Since the competition is about clients submitting videos a movie poster style might be appropriate.

It should be eyecatching and want people to investigate more. A catchy phrase could be 'Lights, Camera, SOLD'. Perhaps this in text in 3D, with lights shining on it, and depth behind it...?? The explanation of the contest could be 'Win the listing services of an exceptional, progressive and dynamic real estate team - a winning video is all we need'.

It should include a pointer for more information to FreeListing.TRHomesDirect.com and the date of Jan 1-June 30, 2014, or email FreeListing@TRHomesDirect.com

We would also use this same design on a A4 size postcard, and print ad.
Updates

Hi folks,

I've just uploaded a zip file of a few iterations of our team logo.  Please note though that the .eps files that I have included have the wrong blue in them.  The correct blue (which is shown in some of the .svg, jpg,.png files) is R 73, G102, B151.

Thank you all very much... looking forward to seeing what you will come up with :-)
Mira

Hello,

thank you for the entries so far.  I am liking what I am seeing.

A few thoughts.  I like the emphasis on the words 'Lights, Camera, SOLD' that I am seeing.  I am liking the incorporation of movie lighting and movie cameras as well. I also like the depth, and 3D components that I've seen in some. 

I've seen designs which have no visual of homes for sale, and some which have stock photos of homes for sale, but am now thinking that we do need some visual representation of the fact that the team sell houses.  When there are no houses in the posters then you actually have to read the text to see that we sell houses if you don't know us, but we want people to get the fact that we sell real estate immediately from first glance... so we should somehow get some visuals of houses in here also.

Some nice homes which have Images that I own, and also videos that I own, are at www.42Brenthold.com, www.8Corliss.com, www63Ashworth.com ...perhaps something of one of these can be incorporated in to give some visuals?

Thanks so much for your efforts
Mira

Hey folks,
I've just uploaded some more photos. 
With some designs that are featuring photos of houses that we have sold very prominently we perhaps should use photos of my own home instead because I am concerned about the new owners protesting about including photos of their home in the poster.  If the photo is small, or transparent it is not as much of a concern, but where it is prominent it may be more appropriate to use a photo/s where we know the owner won't complain (me :-) ).
I also added a couple of photos of the team in case you wanted to use photos of the team in your design... it is not necessary, but I'd prefer the team versus anonymous people :-)
Thanks again for all submissions... I'm so pleased with what we are getting submitted...!
Thanks
Mira 

Target Market(s)

Homeowners aged 30-55+ who are comfortable with technology. Our main demographic are well educated and have professional occupations.

Industry/Entity Type

Progressive

Requirements
Must have
• It should include a link for more information of FreeListing.TRHomesDirect.com and the date of Jan 1-June 30, 2014. Or to email FreeListing@TRHomesDirect.com
Must have our logo incorporated somewhere on the poster.
Nice to have
• Like to show depth in the poster...perhaps a background, then the 3D words of 'Lights, Camera, SOLD', and perhaps a couple of lights and movie camera in the foreground? We're open but in posters that I have seen while looking for ideas I like the ones with some depth to them.
Like blues, and blue tones with some other colors that 'pop'.
Eyecatching.
Would be great to have the explanation of the contest incorporated somewhere on the poster so that people get the idea immediately of what its all about 'Win the listing services of an exceptional, progressive and dynamic real estate team - a winning video is all we need'

```html
<!DOCTYPE html>
<html lang="en">
<head>
<meta charset="utf-8">
<title>Lights, Camera, Sold – TRHomesDirect.com Free Listing Competition</title>
<link rel="stylesheet" href="https://fonts.googleapis.com/css2?family=Anton&family=Montserrat:wght@700;800&family=Oswald:wght@500&family=Open+Sans:wght@400;600&display=swap">
<style>
  :root {
    --charcoal: #2b2c2e;
    --panel-top: #2f3032;
    --panel-mid: #55575a;
    --panel-bottom: #3a3b3d;
    --board-light: #d6d7d9;
    --sky-deep: #1c4f9c;
    --aqua: #6fe0f0;
    --aqua-dark: #14748a;
    --aqua-deeper: #0d4d5e;
    --brand-blue: #496697;
    --white: #ffffff;
    --yellow: #f4e04d;
    --date-cyan: #6ed8ea;
  }
  html, body {
    margin: 0;
    padding: 0;
    overflow: hidden;
    background: #e9ecef;
  }
  .poster {
    position: relative;
    width: 927px;
    height: 1200px;
    overflow: hidden;
    background: var(--sky-deep);
    font-family: "Open Sans", sans-serif;
  }
  .backdrop {
    position: absolute;
    inset: 0;
  }

  /* brand */
  .brand {
    position: absolute;
    left: 60px;
    top: 34px;
    display: flex;
    align-items: center;
    gap: 14px;
  }
  .brand-square {
    width: 52px;
    height: 52px;
    background: var(--white);
    border-radius: 4px;
  }
  .brand-name {
    font-family: "Montserrat", sans-serif;
    font-weight: 700;
    font-size: 32px;
    color: var(--white);
    line-height: 1;
  }
  .brand-tagline {
    position: absolute;
    left: 126px;
    top: 92px;
    font-size: 16px;
    color: var(--white);
    transform: rotate(-2deg);
  }

  /* video players */
  .player {
    position: absolute;
    background: #111214;
    border: 3px solid #55585c;
    border-radius: 8px;
    box-shadow: 0 10px 18px rgba(0,0,0,.55);
    padding: 6px 6px 0;
    box-sizing: border-box;
  }
  .player-screen {
    width: 100%;
    height: 74%;
    border-radius: 3px;
  }
  .player-bar {
    display: flex;
    align-items: center;
    gap: 8px;
    height: 26%;
    padding: 0 6px;
  }
  .player-play {
    width: 0; height: 0;
    border-left: 10px solid #d8d8d8;
    border-top: 6px solid transparent;
    border-bottom: 6px solid transparent;
  }
  .player-track {
    flex: 1;
    height: 4px;
    background: #7a7a7a;
    position: relative;
    border-radius: 2px;
  }
  .player-track::before {
    content: "";
    position: absolute;
    left: 0; top: 0; bottom: 0;
    width: 55%;
    background: #d62b2b;
    border-radius: 2px;
  }
  .player-knob {
    position: absolute;
    left: 53%;
    top: -4px;
    width: 12px; height: 12px;
    border-radius: 50%;
    background: #e6e6e6;
  }
  .player-dot {
    width: 12px; height: 12px;
    border-radius: 50%;
    background: #d8d8d8;
  }
  .player--one { left: 60px; top: 142px; width: 218px; height: 130px; transform: rotate(-3deg); }
  .player--two { left: 345px; top: 132px; width: 218px; height: 130px; transform: rotate(-2deg); }
  .player--three { left: 630px; top: 98px; width: 240px; height: 138px; transform: rotate(-4deg); }
  .screen-house-sale { background: linear-gradient(180deg, #8fb7dc 0%, #b79a6e 55%, #4d7a32 100%); }
  .screen-house-stone { background: linear-gradient(180deg, #a9c6e4 0%, #c9b493 55%, #8a7a62 100%); }
  .screen-house-pool { background: linear-gradient(180deg, #5aa8e8 0%, #e8eef2 50%, #2fb6d8 100%); }

  /* photo and illustration areas */
  .area {
    position: absolute;
  }
  .reel-art {
    left: 0; top: 400px; width: 240px; height: 300px;
    background: radial-gradient(circle at 40% 45%, rgba(160,200,240,.55), rgba(40,100,170,0) 70%);
  }
  .house-photo {
    left: 0; top: 800px; width: 230px; height: 400px;
    background: linear-gradient(180deg, #6f93c0 0%, #9fb3c9 45%, #c9d2da 70%, #4f6a3e 100%);
  }
  .clapperboard {
    left: 202px; top: 362px;
    width: 660px; height: 838px;
    background: linear-gradient(180deg, var(--board-light) 0px, #9a9b9d 60px, var(--panel-top) 80px, var(--panel-mid) 62%, var(--panel-bottom) 100%);
    box-shadow: 0 0 24px rgba(0,0,0,.5);
  }
  .spot-glow {
    position: absolute;
    left: 250px; top: 560px;
    width: 580px; height: 330px;
    background: radial-gradient(ellipse at center, rgba(255,255,255,.28) 0%, rgba(255,255,255,.08) 45%, rgba(255,255,255,0) 70%);
  }
  .spotlight-left {
    left: 90px; top: 590px; width: 240px; height: 610px;
    background: radial-gradient(ellipse 50% 16% at 55% 16%, rgba(20,20,22,.85) 0%, rgba(20,20,22,.45) 60%, rgba(20,20,22,0) 100%),
                linear-gradient(180deg, rgba(20,20,22,0) 25%, rgba(20,20,22,.25) 60%, rgba(20,20,22,0) 100%);
  }
  .spotlight-right {
    left: 790px; top: 590px; width: 137px; height: 610px;
    background: radial-gradient(ellipse 60% 16% at 55% 16%, rgba(20,20,22,.85) 0%, rgba(20,20,22,.45) 60%, rgba(20,20,22,0) 100%),
                linear-gradient(180deg, rgba(20,20,22,0) 25%, rgba(20,20,22,.25) 60%, rgba(20,20,22,0) 100%);
  }

  /* headline */
  .headline {
    position: absolute;
    left: 218px; top: 430px;
    width: 640px;
    margin: 0;
    text-align: center;
    font-family: "Anton", sans-serif;
    font-weight: 400;
    color: var(--aqua);
    -webkit-text-stroke: 2px var(--aqua-deeper);
  }
  .headline-lead {
    display: block;
    font-size: 70px;
    line-height: 1.15;
    letter-spacing: 2px;
    text-shadow: 1px 1px 0 var(--aqua-dark), 2px 2px 0 var(--aqua-dark), 3px 3px 0 var(--aqua-dark), 4px 4px 0 var(--aqua-deeper), 6px 8px 10px rgba(0,0,0,.6);
  }
  .headline-sold {
    display: block;
    font-size: 232px;
    line-height: 1;
    letter-spacing: 6px;
    -webkit-text-stroke: 4px var(--aqua-deeper);
    text-shadow: 2px 2px 0 var(--aqua-dark), 4px 4px 0 var(--aqua-dark), 6px 6px 0 var(--aqua-dark), 8px 8px 0 var(--aqua-deeper), 10px 14px 18px rgba(0,0,0,.6);
  }

  /* copy */
  .copy {
    position: absolute;
    left: 218px; top: 800px;
    width: 640px;
    text-align: center;
  }
  .pitch {
    margin: 0;
    font-family: "Montserrat", sans-serif;
    font-weight: 800;
    font-size: 21px;
    line-height: 1.22;
    color: var(--white);
    text-transform: uppercase;
  }
  .tagline {
    margin: 14px 0 0;
    font-family: "Oswald", sans-serif;
    font-weight: 500;
    font-size: 26px;
    letter-spacing: 1px;
    color: var(--yellow);
  }
  .dates {
    margin: 18px 0 0;
    font-family: "Oswald", sans-serif;
    font-weight: 500;
    font-size: 32px;
    letter-spacing: 1px;
    color: var(--date-cyan);
  }
  .contact {
    margin: 16px 0 0;
    font-size: 20px;
    line-height: 1.35;
    color: var(--white);
  }
  .contact-label {
    color: var(--yellow);
  }

  /* corner brand */
  .corner-brand {
    position: absolute;
    right: 96px; bottom: 28px;
    display: flex;
    align-items: center;
    gap: 8px;
  }
  .corner-square {
    width: 40px; height: 40px;
    background: var(--brand-blue);
    border-radius: 3px;
  }
  .corner-name {
    font-family: "Montserrat", sans-serif;
    font-weight: 700;
    font-size: 13px;
    color: var(--white);
  }
</style>
</head>
<body>
<main class="poster">
  <svg class="backdrop" width="927" height="1200" viewBox="0 0 927 1200" aria-hidden="true">
    <defs>
      <linearGradient id="sky" x1="0" y1="0" x2="1" y2="1">
        <stop offset="0" stop-color="#2f86cf"/>
        <stop offset="0.5" stop-color="#1c56a4"/>
        <stop offset="1" stop-color="#3aa9d8"/>
      </linearGradient>
      <linearGradient id="ribbon" x1="0" y1="0" x2="1" y2="0">
        <stop offset="0" stop-color="#3fb3cf"/>
        <stop offset="0.6" stop-color="#7fe2ee"/>
        <stop offset="1" stop-color="#bff4f8"/>
      </linearGradient>
      <linearGradient id="top" x1="0" y1="0" x2="0" y2="1">
        <stop offset="0" stop-color="#2a2b2d"/>
        <stop offset="1" stop-color="#3b3d40"/>
      </linearGradient>
    </defs>
    <rect width="927" height="1200" fill="url(#sky)"/>
    <path d="M0 330 C300 300 600 300 927 270 L927 520 C620 470 320 420 0 470 Z" fill="url(#ribbon)" opacity="0.85"/>
    <path d="M0 0 H927 V300 C620 320 300 330 0 360 Z" fill="url(#top)"/>
    <path d="M0 360 C300 330 620 320 927 300" fill="none" stroke="#6fd8ea" stroke-width="3" opacity="0.7"/>
  </svg>

  <div class="brand">
    <span class="brand-square"></span>
    <span class="brand-name">TRHomesDirect.com</span>
  </div>
  <div class="brand-tagline">A Data Driven approach to real estate</div>

  <div class="player player--one">
    <div class="player-screen screen-house-sale" role="img" aria-label="Photo of a family house with a for-sale sign on the lawn"></div>
    <div class="player-bar"><span class="player-play"></span><span class="player-track"><span class="player-knob"></span></span><span class="player-dot"></span></div>
  </div>
  <div class="player player--two">
    <div class="player-screen screen-house-stone" role="img" aria-label="Photo of a stone two-storey home with a garage"></div>
    <div class="player-bar"><span class="player-play"></span><span class="player-track"><span class="player-knob"></span></span><span class="player-dot"></span></div>
  </div>
  <div class="player player--three">
    <div class="player-screen screen-house-pool" role="img" aria-label="Photo of a modern villa with a pool and palm tree"></div>
    <div class="player-bar"><span class="player-play"></span><span class="player-track"><span class="player-knob"></span></span><span class="player-dot"></span></div>
  </div>

  <div class="area reel-art" role="img" aria-label="Illustration of a film reel and film strip fading into the blue background"></div>
  <div class="area house-photo" role="img" aria-label="Photo of a large blue-grey colonial house with white columns"></div>

  <div class="area clapperboard" role="img" aria-label="Illustration of a film clapperboard, striped clapper stick on top of a dark slate"></div>
  <div class="spot-glow"></div>

  <div class="area spotlight-left" role="img" aria-label="Illustration of a film spotlight on a tripod shining toward the headline"></div>
  <div class="area spotlight-right" role="img" aria-label="Illustration of a second film spotlight on a tripod shining toward the headline"></div>

  <h1 class="headline">
    <span class="headline-lead">LIGHTS, CAMERA,</span>
    <span class="headline-sold">SOLD</span>
  </h1>

  <section class="copy">
    <p class="pitch">Win the listing services of an<br>exceptional, progressive and<br>dynamic real estate team.</p>
    <p class="tagline">A WINNING VIDEO IS ALL WE NEED</p>
    <p class="dates">JAN 1,2014 - JUNE 30, 2014</p>
    <p class="contact">
      <span class="contact-label">VISIT:</span> FreeListing.TRHomesDirect.com<br>
      <span class="contact-label">OR EMAIL:</span> FreeListing@TRHomesDirect.com
    </p>
  </section>

  <div class="corner-brand">
    <span class="corner-square"></span>
    <span class="corner-name">TRHomesDirect.com</span>
  </div>
</main>
</body>
</html>
```